Google Form Graphic to suit our Brand and industry

Create a graphic / image for us to put at the top of our client enquiry google form.
The image will be a section of an architectural home with our branding over the top. Preferably translucent.
The image must suit the shape of the google forms image, which is an elongated rectangle
#003d5d - brand colour

Target Market(s)

residential home owners, high end architectural homes

Industry/Entity Type

Residential construction

Colors
0054AA
0677BA
7BADD7
CADEEF
E8F1F8

Requirements
Must have
• our branding and a photo of an architectural home in the background

```html
<!DOCTYPE html>
<html lang="en">
<head>
<meta charset="utf-8">
<title>Halden Homes – Client Enquiry Header</title>
<link rel="stylesheet" href="https://fonts.googleapis.com/css2?family=Montserrat:wght@400&display=swap">
<style>
  :root {
    --brand-navy: #003d5d;
    --facade-deep: #123e5e;
    --facade-mid: #1f5479;
    --facade-light: #2d6690;
    --text-white: #ffffff;
  }
  html, body {
    margin: 0;
    padding: 0;
    width: 1200px;
    height: 300px;
    overflow: hidden;
    background: var(--brand-navy);
  }
  .header-banner {
    position: relative;
    width: 1200px;
    height: 300px;
    overflow: hidden;
  }
  .facade-photo {
    position: absolute;
    inset: 0;
    background: linear-gradient(100deg, var(--facade-deep) 35%, var(--facade-mid) 65%, var(--facade-light) 100%);
  }
  .brand-panel {
    position: absolute;
    inset: 0;
    width: 1200px;
    height: 300px;
  }
  .brand-name {
    position: absolute;
    left: 0;
    top: 114px;
    width: 1200px;
    margin: 0;
    padding-left: 0.3em;
    box-sizing: border-box;
    text-align: center;
    font-family: "Montserrat", sans-serif;
    font-weight: 400;
    font-size: 68px;
    line-height: 70px;
    letter-spacing: 0.3em;
    color: var(--text-white);
    white-space: nowrap;
  }
</style>
</head>
<body>
  <header class="header-banner">
    <div class="facade-photo" role="img" aria-label="Close view of a modern architectural home facade with perforated metal screens and dark cladding panels, tinted blue"></div>
    <svg class="brand-panel" viewBox="0 0 1200 300" aria-hidden="true">
      <path d="M0 0 H620 L442 122 Q424 150 442 178 L536 300 H0 Z" fill="var(--brand-navy)"/>
    </svg>
    <h1 class="brand-name">HALDEN HOMES</h1>
  </header>
</body>
</html>
```